Halvery Construction Group Website

Need a dynamic corporate website that can be built on with time. We want to get our information out to the world and have a place where customers can submit requests for proposals.

Target Market(s)

Custom home owners and buyers. Architects and Real Estate Agents.

Industry/Entity Type

Construction

Number of Pages Required

3 page

Font styles to use
Serif
Sans Serif

Requirements
Must have
• Company logo, about, company contact information, biography, contact, projects,
• Sleek, modern, clean, attractive design.
• Online form customers can use for filling out a request for project proposal.
• Linkedin hyperlink.
• Uses www.halveryconstructiongroup.example

```html
<!DOCTYPE html>
<html lang="en">
<head>
<meta charset="utf-8">
<title>Halvery Construction Group</title>
<link rel="stylesheet" href="https://fonts.googleapis.com/css2?family=Exo+2:wght@600;700&family=Lora:ital@0;1&family=Arimo&display=swap">
<style>
:root{
  --hero-dark:#2a2f36;
  --hero-mid:#4a4f56;
  --hero-warm:#5a5048;
  --white:#ffffff;
  --accent:#4aa3df;
  --panel:#f6f7f9;
  --heading:#4b5157;
  --body-text:#6b7075;
  --bar:#0a4f9c;
}
*{margin:0;padding:0;box-sizing:border-box}
html,body{width:1200px;height:909px;overflow:hidden}
body{position:relative;background:var(--panel);font-family:"Arimo",sans-serif}
.hero{position:absolute;left:0;top:0;width:1200px;height:608px;
  background:linear-gradient(180deg,var(--hero-dark) 0%,var(--hero-mid) 45%,var(--hero-warm) 85%,#3a352f 100%)}
.brand{position:absolute;left:86px;top:44px;display:flex;align-items:center;gap:14px;
  font-family:"Exo 2",sans-serif;font-weight:700;font-size:38px;line-height:56px;color:var(--white);letter-spacing:1px}
.brand-mark{width:58px;height:56px;background:var(--white);border-radius:8px}
.nav{position:absolute;top:63px;left:0;width:1200px;height:20px}
.nav a{position:absolute;font-family:"Exo 2",sans-serif;font-weight:600;font-size:14.5px;color:var(--white);text-decoration:none;letter-spacing:.3px}
.nav a.active{color:var(--accent)}
.search{position:absolute;left:1066px;top:48px;width:48px;height:48px;border:2px solid var(--white);border-radius:50%;display:flex;align-items:center;justify-content:center}
.hero-title{position:absolute;top:250px;left:0;width:1200px;text-align:center;font-family:"Exo 2",sans-serif;font-weight:700;font-size:38px;color:var(--white);letter-spacing:.5px}
.hero-title span{color:var(--accent)}
.hero-text{position:absolute;top:314px;left:270px;width:660px;text-align:center;font-family:"Lora",serif;font-style:italic;font-size:12.9px;line-height:26px;color:var(--white)}
.hero-button{position:absolute;left:489px;top:415px;width:222px;height:42px;border:1px solid var(--white);border-radius:3px;
  display:flex;align-items:center;justify-content:center;font-family:"Lora",serif;font-size:13.5px;color:var(--white);text-decoration:none}
.col{position:absolute;top:640px}
.col h3{font-family:"Exo 2",sans-serif;font-weight:600;font-size:17px;color:var(--heading);letter-spacing:.3px;margin-bottom:22px}
.col ul{list-style:none}
.col li{font-size:12.5px;color:var(--body-text);height:28.3px;padding-left:19px;position:relative}
.col li::before{content:"»";position:absolute;left:0;top:-1px;font-size:13px}
.col p{font-size:12.2px;line-height:24px;color:var(--body-text);width:520px;margin-left:4px;margin-top:-5px}
.bar{position:absolute;left:0;top:849px;width:1200px;height:60px;background:var(--bar)}
.copyright{position:absolute;left:87px;top:22px;font-size:12.5px;color:var(--white)}
.social{position:absolute;top:12px;width:36px;height:36px;border:2px solid var(--white);border-radius:50%}
</style>
</head>
<body>
<section class="hero" role="img" aria-label="Photo of a city skyline under construction with tower cranes and high-rise buildings at dusk"></section>

<header>
  <div class="brand"><span class="brand-mark"></span>HALVERY</div>
  <nav class="nav">
    <a class="active" href="#" style="left:603px">HOME</a>
    <a href="#" style="left:688px">ABOUT</a>
    <a href="#" style="left:780px">BIO</a>
    <a href="#" style="left:849px">PROJECTS</a>
    <a href="#" style="left:964px">CONTACT US</a>
  </nav>
  <div class="search" aria-label="Search">
    <svg width="14" height="14" viewBox="0 0 14 14"><circle cx="5.8" cy="5.8" r="4.2" fill="none" stroke="#fff" stroke-width="2"/><line x1="9" y1="9" x2="12.5" y2="12.5" stroke="#fff" stroke-width="2.2" stroke-linecap="round"/></svg>
  </div>
</header>

<h1 class="hero-title">HALVERY <span>CONSTRUCTION</span> GROUP</h1>
<p class="hero-text">Sed ut perspiciatis unde omnis iste natus error sit voluptatem accusantium doloremque laudantium,<br>totam rem aperiam, eaque ipsa quae ab illo inventore veritatis et quasi architecto beatae vitae dicta sunt<br>con sequuntur magni dolores eos qui ratione voluptatem sequi nesciunt.</p>
<a class="hero-button" href="#">CLICK HERE FOR MORE INFO</a>

<div class="col" style="left:86px"><h3>PROJECTS</h3><ul><li>Commercial</li><li>Residential</li><li>Community</li><li>Location Map</li></ul></div>
<div class="col" style="left:250px"><h3>PROFILE</h3><ul><li>Team</li><li>Process</li><li>Testimonials</li><li>History</li></ul></div>
<div class="col" style="left:404px"><h3>CONNECT</h3><ul><li>Home</li><li>About,</li><li>Bio</li><li>Projects</li><li>Contact us</li></ul></div>
<div class="col" style="left:577px"><h3>COMMERCIAL, RESIDENTIAL AND COMMUNITY SOLUTIONS</h3>
  <p>Sed ut perspiciatis unde omnis iste natus error sit voluptatem accusantium doloremque laudan<br>tium, totam rem aperiam, eaque ipsa quae ab illo inventore veritatis et quasi architecto beatae vit<br>ae dicta sunt explicabo. Nemo enim ipsam voluptatem quia voluptas sit aspernatur aut dolores<br>eos qui ratione voluptatem sequi nesciunt.</p></div>

<footer class="bar">
  <div class="copyright">© 2016 Copyrights.Halvery Construction Group.All Rights Reserved.</div>
  <a class="social" href="#" aria-label="Social profile" style="left:908px"></a>
  <a class="social" href="#" aria-label="Social profile" style="left:951px"></a>
  <a class="social" href="#" aria-label="Social profile" style="left:993px"></a>
  <a class="social" href="#" aria-label="Professional network profile" style="left:1036px"></a>
  <a class="social" href="#" aria-label="Video channel" style="left:1079px"></a>
</footer>
</body>
</html>
```